Album art design concept, my band will be releasing a 11 song rock album in the next few Months. We will be using it as a CD cover, poster, online art cover, maybe even Vinyl. Working album titles are "Woven from static" (Preferred album title) or "The river under the stone". Anything abstract, painting-like design, or whatever type of design that comes to mind. Fonts are designers choice. Thank You

Target Market(s)

Music business

Colors

Designer to choose colors to be used in the design.

Requirements
Must have
• Our band logo
Nice to have
• Anything abstract, attractive painting type, maybe even some kind of a futuristic design.
Should not have
• Skulls, blood-like, scary designs, nudity, emo type of design

```html
<!DOCTYPE html>
<html lang="en">
<head>
<meta charset="utf-8">
<title>Woven from static — Copper Lantern</title>
<link rel="stylesheet" href="https://fonts.googleapis.com/css2?family=Orbitron:wght@700;900&display=swap">
<style>
  :root {
    --paper: #e0dbdc;
    --ink: #050505;
    --crimson: #e33a4b;
    --rose: #e5606b;
    --oxblood: #6e1a20;
    --ash: #8c8a8a;
    --silver: #c9c7c7;
    --white: #ffffff;
  }
  html, body {
    margin: 0;
    padding: 0;
    overflow: hidden;
    background: var(--paper);
  }
  .cover {
    position: relative;
    width: 1199px;
    height: 1200px;
    overflow: hidden;
    background: var(--paper);
    font-family: "Orbitron", sans-serif;
  }
  .painting {
    position: absolute;
    inset: 0;
  }
  .band-block {
    position: absolute;
    left: 0;
    top: 786px;
    width: 494px;
    height: 414px;
    background: var(--ink);
  }
  .band-name {
    position: absolute;
    left: 52px;
    top: 965px;
    width: 380px;
    margin: 0;
    font-weight: 700;
    font-size: 44px;
    line-height: 1.25;
    letter-spacing: 1px;
    color: var(--silver);
    text-align: right;
  }
  .mark-block {
    position: absolute;
    left: 1022px;
    top: 0;
    width: 177px;
    height: 272px;
    background: var(--ink);
    display: flex;
    flex-direction: column;
    align-items: center;
    justify-content: center;
    gap: 14px;
  }
  .mark-square {
    width: 26px;
    height: 26px;
    background: var(--crimson);
  }
  .mark-name {
    margin: 0;
    font-weight: 700;
    font-size: 17px;
    line-height: 1.4;
    color: var(--crimson);
    text-align: center;
    letter-spacing: 1px;
  }
  .album-title {
    position: absolute;
    inset: 0;
    margin: 0;
    font-weight: 900;
    color: var(--ink);
    -webkit-text-stroke: 2px var(--white);
    paint-order: stroke fill;
    text-transform: uppercase;
  }
  .album-title span {
    position: absolute;
    white-space: nowrap;
    line-height: 1;
  }
  .title-line-1 { left: 44px;  top: 252px; font-size: 96px; }
  .title-line-2 { left: 440px; top: 360px; font-size: 80px; }
  .title-line-3 { left: 560px; top: 438px; font-size: 96px; }
</style>
</head>
<body>
  <main class="cover">
    <svg class="painting" width="1199" height="1200" viewBox="0 0 1199 1200" role="img" aria-label="Abstract painted splash of red, crimson and charcoal ink strokes spreading across the cover">
      <defs>
        <radialGradient id="splash" cx="45%" cy="50%" r="55%">
          <stop offset="0%" stop-color="#6e1a20"/>
          <stop offset="35%" stop-color="#c23343"/>
          <stop offset="70%" stop-color="#e5606b"/>
          <stop offset="100%" stop-color="#e5606b" stop-opacity="0"/>
        </radialGradient>
        <radialGradient id="smoke" cx="60%" cy="80%" r="45%">
          <stop offset="0%" stop-color="#3a3a3a" stop-opacity="0.8"/>
          <stop offset="100%" stop-color="#8c8a8a" stop-opacity="0"/>
        </radialGradient>
      </defs>
      <path d="M120 160 C260 20 620 -20 860 40 C1060 90 1199 300 1180 520 C1160 720 1050 880 900 950 C740 1030 520 1000 330 900 C160 810 40 640 40 460 C40 320 70 220 120 160 Z" fill="url(#splash)"/>
      <ellipse cx="760" cy="960" rx="420" ry="260" fill="url(#smoke)"/>
    </svg>

    <h1 class="album-title">
      <span class="title-line-1">Woven</span>
      <span class="title-line-2">From</span>
      <span class="title-line-3">Static</span>
    </h1>

    <div class="mark-block">
      <div class="mark-square"></div>
      <p class="mark-name">COPPER<br>LANTERN</p>
    </div>

    <div class="band-block"></div>
    <p class="band-name">COPPER<br>LANTERN</p>
  </main>
</body>
</html>
```